Tellmora Corporate Stationery

Look for design of all new corporate stationery for an existing insurance broking business that is going through a redesign and move from older partners to younger family members. New Logo is attached. Company is Brisbane based.
Colours in the Logo is Hex #43bed8 and website features a lot of hex #17b8d8. Website front page "A plan to protect you" - headline. "Professional and Individual advice to protect your greatest assets" - tagline.

Stationery required: Business Cards, Letter head, Thank-you cards, Birthday cards, Presentation folders, With Compliment slips and a powerpoint template. We also would like to send a card to all customers with the something along of the lines of "something new".

Target Market(s)

Customers of Insurance business looking at superannuation, life and income protection insurance, investment advice and wills

Industry/Entity Type

Insurance Broker

Font styles to use
Other font styles liked:
• same as logo

Requirements
Must have
• The above designs for new stationery for the new business including:
• Business Cards, Letter head, Thank-you cards, Birthday cards, Presentation folders, With Compliment slips and a powerpoint template. We also would like to send a card to all customers with the something along of the lines of "something new".
Nice to have
• It is a new look - long time family business being passed to next generation - big focus on advice for YOU, individual advice etc..

```html
<!DOCTYPE html>
<html lang="en">
<head>
<meta charset="utf-8">
<title>Tellmora Business Card</title>
<link href="https://fonts.googleapis.com/css2?family=Open+Sans:wght@400;600&display=swap" rel="stylesheet">
<style>
  :root {
    --brand: #43bed8;
    --brand-deep: #17b8d8;
    --card-back: #3dbfd9;
    --ink: #555a5e;
    --ink-soft: #7a7f83;
    --rule: #a9adb0;
    --paper: #ffffff;
    --stage: #2b2b2b;
  }
  * { box-sizing: border-box; margin: 0; padding: 0; }
  html, body { width: 1200px; height: 987px; overflow: hidden; }
  body {
    background: var(--stage);
    font-family: "Open Sans", Arial, sans-serif;
    position: relative;
  }
  .card {
    position: absolute;
    left: 293px;
    width: 615px;
    height: 351px;
    overflow: hidden;
  }
  .card-front { top: 130px; background: var(--paper); }
  .card-back { top: 505px; background: var(--card-back); }

  .brand-mark {
    position: absolute;
    display: flex;
    align-items: center;
    gap: 12px;
  }
  .card-front .brand-mark { left: 293px; top: 72px; }
  .brand-dot {
    width: 40px; height: 40px; border-radius: 50%;
    background: var(--brand);
  }
  .brand-name {
    font-weight: 600;
    font-size: 34px;
    letter-spacing: 2px;
    text-transform: uppercase;
    color: var(--brand);
    line-height: 1;
  }

  .person { position: absolute; left: 33px; top: 171px; }
  .person-name {
    font-weight: 600; font-size: 21px; color: var(--brand);
    letter-spacing: 0.3px; line-height: 1.2;
  }
  .person-role { font-size: 16px; color: var(--ink-soft); line-height: 1.3; }

  .divider {
    position: absolute; left: 33px; top: 222px;
    width: 559px; height: 1px; background: var(--rule);
  }

  .contact-list { position: absolute; left: 33px; top: 229px; list-style: none; }
  .contact-list li {
    display: flex; align-items: center; gap: 7px;
    font-size: 16px; color: var(--ink); height: 23.5px;
  }
  .contact-list svg { width: 16px; height: 16px; fill: var(--brand); flex: none; }

  .address {
    position: absolute; right: 23px; top: 255px;
    text-align: right; font-size: 16px; color: var(--ink); line-height: 22px;
  }

  .edge-rule { position: absolute; left: 0; bottom: 12px; width: 100%; height: 2px; background: var(--rule); }
  .edge-band { position: absolute; left: 0; bottom: 0; width: 100%; height: 10px; background: var(--brand); }

  .card-back .back-brand { position: absolute; left: 18px; top: 262px; }
  .back-brand .brand-name { color: var(--paper); font-size: 32px; }
  .back-url {
    margin-top: 12px;
    font-size: 15px; color: var(--paper);
    letter-spacing: 5px; font-style: normal;
  }
</style>
</head>
<body>
  <section class="card card-front" aria-label="Business card front">
    <div class="brand-mark">
      <span class="brand-dot"></span>
      <span class="brand-name">Tellmora</span>
    </div>

    <div class="person">
      <p class="person-name">DANIEL REYES</p>
      <p class="person-role">CEO/FOUNDER</p>
    </div>

    <div class="divider"></div>

    <ul class="contact-list">
      <li>
        <svg viewBox="0 0 16 16" aria-hidden="true"><path d="M3.2 1.5l2.3 2.8-1.3 1.6c.9 2.1 2.5 3.7 4.6 4.7l1.6-1.3 2.8 2.3-1.2 2.3C6.6 13.6 2.4 9.4 1.1 2.7z"/></svg>
        612 405 2291
      </li>
      <li>
        <svg viewBox="0 0 16 16" aria-hidden="true"><path d="M4.5 0.5h7a1 1 0 0 1 1 1v13a1 1 0 0 1-1 1h-7a1 1 0 0 1-1-1v-13a1 1 0 0 1 1-1zm.6 2v9.5h5.8V2.5zM8 12.8a.9.9 0 1 0 0 1.8.9.9 0 0 0 0-1.8z"/></svg>
        614 738 5520
      </li>
      <li>
        <svg viewBox="0 0 16 16" aria-hidden="true"><path d="M4 1h7l1 1v4H4zM1.5 6.5h13a1 1 0 0 1 1 1V13a1 1 0 0 1-1 1h-13a1 1 0 0 1-1-1V7.5a1 1 0 0 1 1-1zM4 10h8v1.2H4z"/></svg>
        617 302 4486
      </li>
      <li>
        <svg viewBox="0 0 16 16" aria-hidden="true"><path d="M1 3.5h14v9H1zm1.4 1L8 8.6l5.6-4.1z"/></svg>
        daniel@tellmora.com
      </li>
    </ul>

    <address class="address" style="font-style:normal">
      42 Wattle Grove Street<br>
      Brisbane, Queensland 4000<br>
      www.tellmora.com
    </address>

    <div class="edge-rule"></div>
    <div class="edge-band"></div>
  </section>

  <section class="card card-back" aria-label="Business card back">
    <div class="back-brand">
      <span class="brand-name">Tellmora</span>
      <p class="back-url">www.tellmora.com</p>
    </div>
  </section>
</body>
</html>
```